"Vine Hollow Excursions" is a top notch Santa Barbara County Wine Tour company.

We provide scenic, boutique and custom wine tours. I need the card to be clean and classy. I will provide our logo. I would like the logo to cover the back side of the card as an option and would like to see a couple color options other then our signature green and gold. I would like to see some creative options and let the designers come up with options.
I need cards for myself and my team. The final design should communicate "An authentic and boutique wine tour experience"
Please use my website for reference www.vinehollowexcursions.example

Target Market(s)

We have a wide range of clients from millennials to baby boomers

Industry/Entity Type

Tour

Contact Information for Business Card

Contact info:
Dale Morton
805-219-6384
info@vinehollowexcursions.example
vinehollowexcursions.example

Colors

Designer to choose colors to be used in the design.

Requirements
Must have
• my logo
Nice to have
• *I would like to have the backside side with the logo and the company statement
• "An authentic and boutique wine tour experience" as an option.
• *I would also like to see what the designers can create!
• *I would like to see an option that incorporates or social: instagram, yelp, trip advisor
Should not have
• I do not want it too busy.

```html
<!DOCTYPE html>
<html lang="en">
<head>
<meta charset="utf-8">
<title>Vine Hollow Excursions — Business Card</title>
<link href="https://fonts.googleapis.com/css2?family=Cinzel:wght@500;600&family=Raleway:wght@400;500;600&display=swap" rel="stylesheet">
<style>
  :root {
    --backdrop: #e9e9e7;
    --card-green: #416a48;
    --card-white: #ffffff;
    --ink-light: #f3f5f1;
    --ink-soft: rgba(243, 245, 241, 0.8);
    --rule: rgba(243, 245, 241, 0.55);
  }
  * { margin: 0; padding: 0; box-sizing: border-box; }
  html, body {
    width: 1200px; height: 810px; overflow: hidden;
    background: var(--backdrop);
  }
  .canvas { position: relative; width: 1200px; height: 810px; }
  .card {
    position: absolute; left: 280px; width: 640px; height: 366px;
    background: var(--card-green);
    box-shadow: 0 6px 18px rgba(0,0,0,0.18);
    overflow: hidden;
    color: var(--ink-light);
    font-family: "Raleway", sans-serif;
  }
  .card--front { top: 24px; }
  .card--back { top: 420px; }

  .wordmark {
    display: flex; align-items: center; gap: 12px;
    font-family: "Cinzel", serif; font-weight: 600;
    color: var(--ink-light); letter-spacing: 1.5px; line-height: 1.15;
  }
  .wordmark__dot {
    width: 14px; height: 14px; border-radius: 50%;
    background: var(--ink-light); flex: none;
  }
  .card--front .wordmark {
    position: absolute; left: 0; right: 0; top: 138px;
    justify-content: center; font-size: 30px;
  }
  .social-row {
    position: absolute; left: 0; right: 0; bottom: 48px;
    display: flex; justify-content: center; gap: 22px;
    font-size: 14px; color: var(--ink-soft);
  }
  .social-row__item { display: flex; align-items: center; gap: 7px; white-space: nowrap; }
  .social-row__mark { width: 9px; height: 9px; background: currentColor; flex: none; }
  .social-row__mark--round { border-radius: 50%; }

  .card--back .wordmark {
    position: absolute; left: 40px; top: 100px; width: 230px;
    font-size: 24px;
  }
  .divider {
    position: absolute; left: 296px; top: 64px; width: 1px; height: 160px;
    background: var(--rule);
  }
  .contact { position: absolute; left: 320px; top: 66px; }
  .contact__name {
    font-family: "Cinzel", serif; font-weight: 600;
    font-size: 22px; letter-spacing: 1px; white-space: nowrap;
  }
  .contact__title {
    font-size: 13px; font-weight: 500; letter-spacing: 1px;
    margin: 2px 0 12px 10px;
  }
  .contact__list { list-style: none; margin-left: 20px; }
  .contact__item {
    display: flex; align-items: center; gap: 11px;
    font-size: 13px; color: var(--ink-soft); margin-bottom: 5px;
    white-space: nowrap;
  }
  .contact__item svg { width: 11px; height: 11px; flex: none; }
  .contact__item strong { font-weight: 600; color: var(--ink-light); }

  .footer-band {
    position: absolute; left: 0; right: 0; bottom: 0; height: 76px;
    background: var(--card-white);
    display: flex; justify-content: center; align-items: flex-start;
    padding-top: 14px; gap: 12px;
    font-size: 14px; color: var(--card-green);
  }
  .footer-band__sep { width: 1px; height: 15px; background: var(--card-green); }
</style>
</head>
<body>
<main class="canvas">

  <section class="card card--front" aria-label="Card front">
    <div class="wordmark"><span class="wordmark__dot"></span>Vine Hollow Excursions</div>
    <div class="social-row">
      <span class="social-row__item"><span class="social-row__mark social-row__mark--round"></span>/biz/vinehollowexcursions</span>
      <span class="social-row__item"><span class="social-row__mark"></span>@sbcvinetrips</span>
    </div>
  </section>

  <section class="card card--back" aria-label="Card back">
    <div class="wordmark"><span class="wordmark__dot"></span>Vine Hollow Excursions</div>
    <div class="divider"></div>
    <div class="contact">
      <div class="contact__name">Dale Morton</div>
      <div class="contact__title">TRIP ADVISOR</div>
      <ul class="contact__list">
        <li class="contact__item">
          <svg viewBox="0 0 12 12"><path d="M2.5 1 4.5 1 5.3 3.6 4 4.6Q5 7 7.4 8L8.4 6.7 11 7.5 11 9.5Q10 11 8 10.8 2 9 1.2 3.8 1 2 2.5 1Z" fill="currentColor"/></svg>
          <span>805-219-6384</span>
        </li>
        <li class="contact__item">
          <svg viewBox="0 0 12 12"><rect x="1" y="2.5" width="10" height="7" fill="none" stroke="currentColor" stroke-width="1.2"/><path d="M1 2.5 6 6.5 11 2.5" fill="none" stroke="currentColor" stroke-width="1.2"/></svg>
          <span>info@vinehollowexcursions.example</span>
        </li>
        <li class="contact__item">
          <svg viewBox="0 0 12 12" fill="none" stroke="currentColor" stroke-width="1"><circle cx="6" cy="6" r="5"/><ellipse cx="6" cy="6" rx="2.2" ry="5"/><path d="M1 6H11M2 3.3H10M2 8.7H10"/></svg>
          <span>www.<strong>vinehollowexcursions</strong>.example</span>
        </li>
      </ul>
    </div>
    <div class="footer-band">
      <span class="social-row__item"><span class="social-row__mark"></span>: /vinehollowexcursions</span>
      <span class="footer-band__sep"></span>
      <span class="social-row__item"><span class="social-row__mark"></span>: @vinehollowexcursions</span>
    </div>
  </section>

</main>
</body>
</html>
```